Commercial Post Cards

We are looking for 3 postcards that are similar but target 3 commercial property types. they will be 6x9 cards can be front and back or not.
1. Hotel Postcard – Taviqon / Bed Bug Protection
Use the attached Taviqon sample as the primary direction.
The focus should be:
Proactive bed bug prevention and control
Protecting guests and the hotel's reputation
Regular inspections
Documentation and risk management
Professional commercial pest management
The backside should transition into our General Pest Control services, showing that we can be the hotel's complete pest management provider beyond just bed bugs.
2. Apartment Complex Postcard
Target apartment owners, property managers, and management companies.
Focus on:
General pest control
Bed bug control
Rodent control
Preventative pest management
Protecting residents and the property
Reliable, ongoing service and documentation
The message should position us as a full-service pest management partner for multifamily properties.

3. Commercial Building Postcard
Target office buildings, banks, storage facilities, and other commercial properties.

Focus on:
General commercial pest control
Rodent control
Fly management
Recurring service programs
Protecting the property, employees, customers, and reputation

Overall Direction
All three postcards should have a consistent brand and visual style, but each should feel specifically designed for its target market.

We want the messaging to communicate:
Professional • Reliable • Proactive • Locally Owned & Operated • Serving Since 2017

The goal is not to overwhelm the reader with information. These should be marketing pieces that quickly communicate the problem we solve, our expertise, and why a commercial property should contact us.

I have included some of our marketing materials for help with what we do.

```html
<!DOCTYPE html>
<html lang="en">
<head>
<meta charset="utf-8">
<title>WorkShield Commercial Postcard</title>
<link rel="stylesheet" href="https://fonts.googleapis.com/css2?family=Oswald:wght@400;500;600;700&display=swap">
<style>
  :root{
    --orange:#f15a24;
    --black:#111111;
    --white:#ffffff;
    --page:#e4e4e4;
    --ink:#1a1a1a;
    --line:#3a3a3a;
  }
  *{box-sizing:border-box;margin:0;padding:0}
  html,body{width:1200px;height:598px;overflow:hidden;background:var(--page);font-family:"Oswald",sans-serif;color:var(--ink)}
  .canvas{position:relative;width:1200px;height:598px}
  .card{position:absolute;top:109px;width:570px;height:380px;overflow:hidden}
  .card--front{left:20px;background:var(--orange)}
  .card--back{left:610px;background:var(--white)}

  .brand{position:absolute;display:flex;flex-direction:column}
  .brand__name{font-weight:700;font-size:22px;line-height:1;letter-spacing:.2px}
  .brand__tag{font-weight:400;font-size:9px;letter-spacing:.4px;margin-top:4px;text-transform:uppercase}

  .front__photo{position:absolute;right:0;top:0;width:360px;height:352px;
    background:
      linear-gradient(90deg,var(--orange) 0%,rgba(241,90,36,0) 32%),
      radial-gradient(ellipse at 60% 80%,rgba(240,160,90,.55) 0%,rgba(240,160,90,0) 45%),
      linear-gradient(180deg,#7f9cc4 0%,#4f5f7c 45%,#2c3140 100%)}
  .front__brand{left:20px;top:22px;color:var(--white)}
  .front__brand .brand__tag{color:var(--black)}
  .headline{position:absolute;left:20px;top:92px;font-weight:700;font-size:54px;line-height:1;letter-spacing:-1px;text-transform:uppercase}
  .headline__dark{color:var(--black)}
  .headline__light{color:var(--white)}
  .promise{position:absolute;left:0;top:152px;width:292px;height:59px;background:var(--white);padding:3px 0 0 20px;font-weight:600;font-size:21px;line-height:1.2;color:var(--black);text-transform:uppercase}
  .subline{position:absolute;left:20px;top:218px;font-weight:400;font-size:10.5px;line-height:1.35;color:var(--white);text-transform:uppercase}
  .services{position:absolute;left:0;top:251px;width:340px;height:66px}
  .services__panel{position:absolute;inset:0}
  .services__grid{position:absolute;left:14px;top:5px;display:grid;grid-template-columns:95px 82px 110px;row-gap:6px}
  .service{display:flex;align-items:center;gap:6px;font-weight:500;font-size:9.5px;line-height:1.1;text-transform:uppercase;color:var(--black)}
  .service__icon{width:22px;height:22px;background:var(--orange);border-radius:2px;display:flex;align-items:center;justify-content:center;flex:none}
  .bar{position:absolute;left:0;bottom:0;width:100%;height:28px;display:flex;align-items:center;justify-content:center;gap:12px;font-weight:500;font-size:12px;text-transform:uppercase;letter-spacing:.1px}
  .bar--dark{background:var(--black);color:var(--white)}
  .bar--orange{background:var(--orange);color:var(--white)}
  .bar__sep{width:1px;height:16px;background:currentColor}

  .back__brand{left:20px;top:28px;color:var(--black)}
  .back__brand .brand__name{color:var(--orange)}
  .coverage{position:absolute;left:16px;top:86px;font-weight:700;font-size:21px;line-height:1.08;color:var(--orange);text-transform:uppercase}
  .pests{position:absolute;left:16px;top:140px;width:280px;display:flex;flex-wrap:wrap;row-gap:10px;font-size:9px;text-transform:uppercase;color:var(--orange);list-style:none}
  .pest{display:flex;align-items:center;gap:4px;padding:0 6px;border-right:1px solid var(--ink)}
  .pest:first-child,.pest--row{padding-left:0}
  .pest--end,.pest:last-child{border-right:0}
  .pest__dot{width:8px;height:8px;border-radius:50%;background:var(--orange)}
  .cta{position:absolute;left:0;top:204px;width:287px;height:70px;background:var(--black);padding:5px 0 0 13px;text-transform:uppercase}
  .cta__lead{font-weight:700;font-size:29px;line-height:1;color:var(--orange)}
  .cta__sub{font-weight:500;font-size:19px;line-height:1.2;color:var(--white);margin-top:3px}
  .contacts{position:absolute;left:20px;top:281px;display:grid;grid-template-columns:146px 130px;row-gap:8px}
  .contact{display:flex;align-items:center;gap:5px;font-weight:500;font-size:10.5px;color:var(--black)}
  .contact__icon{width:18px;height:18px;flex:none}
  .divider{position:absolute;left:306px;top:20px;width:1px;height:318px;background:var(--line)}
  .stamp{position:absolute;left:459px;top:38px;width:78px;height:90px;border:1px solid var(--line)}
  .address-line{position:absolute;left:326px;width:224px;height:1px;background:var(--line)}
</style>
</head>
<body>
<main class="canvas">

  <section class="card card--front" aria-label="Postcard front">
    <div class="front__photo" role="img" aria-label="Photo of a modern glass commercial office building lit at dusk"></div>

    <div class="brand front__brand">
      <span class="brand__name">Ridgeline Pest Control</span>
      <span class="brand__tag">Keeping pests out for good</span>
    </div>

    <h1 class="headline"><span class="headline__dark">WORK</span><span class="headline__light">SHIELD</span></h1>

    <p class="promise">Protect your guests.<br>Protect your reputation.</p>

    <p class="subline">Reliable commercial pest control<br>you can count on.</p>

    <div class="services">
      <svg class="services__panel" viewBox="0 0 340 66" preserveAspectRatio="none" aria-hidden="true">
        <polygon points="0,0 340,0 290,66 0,66" fill="#ffffff"/>
      </svg>
      <div class="services__grid">
        <div class="service">
          <span class="service__icon"><svg width="14" height="14" viewBox="0 0 14 14" fill="none" stroke="#fff" stroke-width="1.2"><ellipse cx="7" cy="8" rx="2.2" ry="3.6" fill="#fff"/><path d="M2 4l3 2M12 4l-3 2M1.5 8h3M12.5 8h-3M2 12l3-2M12 12l-3-2"/></svg></span>
          <span>General pest<br>control</span>
        </div>
        <div class="service">
          <span class="service__icon"><svg width="14" height="14" viewBox="0 0 14 14" fill="none" stroke="#fff" stroke-width="1.2"><ellipse cx="7" cy="8" rx="3" ry="4" fill="#fff"/><circle cx="7" cy="3" r="1.4" fill="#fff"/></svg></span>
          <span>Bed bug<br>control</span>
        </div>
        <div class="service">
          <span class="service__icon"><svg width="14" height="14" viewBox="0 0 14 14" fill="none" stroke="#fff" stroke-width="1.3"><path d="M7 1.5l5 2v3.5c0 3-2.2 5-5 5.8C4.2 12 2 10 2 7V3.5z"/><path d="M4.6 7l1.8 1.8L9.6 5.6"/></svg></span>
          <span>Preventative<br>programs</span>
        </div>
        <div class="service">
          <span class="service__icon"><svg width="14" height="14" viewBox="0 0 14 14" fill="none" stroke="#fff" stroke-width="1.2"><rect x="3" y="2.5" width="8" height="10" rx="1"/><path d="M5 2h4v1.5H5zM5 6h4M5 8.2h4M5 10.4h3"/></svg></span>
          <span>Documented<br>service</span>
        </div>
        <div class="service">
          <span class="service__icon"><svg width="14" height="14" viewBox="0 0 14 14" fill="#fff"><ellipse cx="7" cy="8.5" rx="4.5" ry="2.8"/><circle cx="3" cy="6.5" r="1.3"/><path d="M11.5 8.5c1.5 0 2 1 1.8 2" stroke="#fff" fill="none"/></svg></span>
          <span>Rodent<br>control</span>
        </div>
      </div>
    </div>

    <div class="bar bar--dark">
      <span>Professional. Reliable. Proactive.</span><span class="bar__sep"></span>
      <span>Serving since 2017</span><span class="bar__sep"></span>
      <span>Locally owned &amp; operated</span>
    </div>
  </section>

  <section class="card card--back" aria-label="Postcard back">
    <div class="brand back__brand">
      <span class="brand__name">Ridgeline Pest Control</span>
      <span class="brand__tag">Keeping pests out for good</span>
    </div>

    <h2 class="coverage">Complete pest protection for<br>your entire property</h2>

    <ul class="pests" aria-label="Pests covered">
      <li class="pest"><span class="pest__dot"></span>Spiders</li>
      <li class="pest"><span class="pest__dot"></span>Cockroaches</li>
      <li class="pest"><span class="pest__dot"></span>Ants</li>
      <li class="pest pest--end"><span class="pest__dot"></span>Silverfish</li>
      <li class="pest pest--row"><span class="pest__dot"></span>Pantry pests</li>
      <li class="pest"><span class="pest__dot"></span>Rodents</li>
      <li class="pest"><span class="pest__dot"></span>Flies</li>
      <li class="pest"><span class="pest__dot"></span>Wasps</li>
    </ul>

    <div class="cta">
      <p class="cta__lead">Call or email</p>
      <p class="cta__sub">For a custom quote today!</p>
    </div>

    <div class="contacts">
      <div class="contact">
        <svg class="contact__icon" viewBox="0 0 18 18" fill="none" stroke="#f15a24" stroke-width="1.3"><circle cx="9" cy="9" r="8"/><path d="M6 5l1.6 2.2-.9 1.2c.6 1.2 1.5 2.1 2.7 2.7l1.2-.9L12.8 12l-1 1.2C8.5 13 5 9.5 4.8 6.2z"/></svg>
        <span>555-310-4820 (Office)</span>
      </div>
      <div class="contact">
        <svg class="contact__icon" viewBox="0 0 18 18" fill="none" stroke="#f15a24" stroke-width="1.3"><circle cx="9" cy="9" r="8"/><rect x="6.3" y="4" width="5.4" height="10" rx="1"/><path d="M8.3 12.2h1.4"/></svg>
        <span>555-310-7716 (Cell)</span>
      </div>
      <div class="contact">
        <svg class="contact__icon" viewBox="0 0 18 18" fill="none" stroke="#f15a24" stroke-width="1.3"><circle cx="9" cy="9" r="8"/><rect x="4.8" y="6" width="8.4" height="6" rx=".6"/><path d="M4.8 6.2L9 9.4l4.2-3.2"/></svg>
        <span>office@ridgelinepest.com</span>
      </div>
      <div class="contact">
        <svg class="contact__icon" viewBox="0 0 18 18" fill="none" stroke="#f15a24" stroke-width="1.2"><circle cx="9" cy="9" r="8"/><circle cx="9" cy="9" r="4.6"/><path d="M4.4 9h9.2M9 4.4c-2 2.6-2 6.6 0 9.2M9 4.4c2 2.6 2 6.6 0 9.2"/></svg>
        <span>www.ridgelinepest.com</span>
      </div>
    </div>

    <div class="divider"></div>
    <div class="stamp" aria-label="Postage area"></div>
    <div class="address-line" style="top:149px"></div>
    <div class="address-line" style="top:185px"></div>
    <div class="address-line" style="top:220px"></div>

    <div class="bar bar--orange">
      <span>Professional. Reliable. Proactive.</span><span class="bar__sep"></span>
      <span>Serving since 2017</span><span class="bar__sep"></span>
      <span>Locally owned &amp; operated</span>
    </div>
  </section>

</main>
</body>
</html>
```